Business card for denture clinic Veltrimora

We need a new business card with our new logo. We are a denture clinic in New Zealand with our target market being 45+ years old. We would need a space on the back to write our patients next appointment on. We would space for only one appointment rather than a list. We will attach a photo showing an example of this. But of course, we would like to see your twist on this. We want it to be bold and easy to read and a good mixture of professional but modern. We have attached our logo to be used on the card.

Target Market(s)

People aged 45+ needing dentures

Industry/Entity Type

Dental

Contact Information for Business Card

We want our logo on the front and the space to write an appointment on the back. I've attached an example our our old business card showing this. We need to have the technicians details on the front.

Font styles to use
Sans Serif

Colors
0255a3
919191
fbfbfb

Requirements
Must have
• The following details:
• Liam Dorsett BDT, PGDipCDentTech Calverin
• Dental Prosthetist
• Phone numbers: 0800 47 3125
• 09 572 1394
• Email: liam@veltrimora.co.nz
• www.veltrimora.co.nz
• Address: 14 Marlow Crest Road
• Halbrook West
• Auckland 0793
Nice to have
• We would like our business cards to have more than just two colours as we want them to be more vibrant. We have uploaded an example of a business card we liked that showed this.

```html
<!DOCTYPE html>
<html lang="en">
<head>
<meta charset="UTF-8">
<title>Veltrimora – Business Card</title>
<link rel="stylesheet" href="https://fonts.googleapis.com/css2?family=Open+Sans:ital,wght@0,400;0,600;0,700;1,400&display=swap">
<style>
  :root {
    --brand-blue: #0070bb;
    --brand-deep: #0255a3;
    --text-grey: #5a5a5a;
    --rule-grey: #919191;
    --card-white: #fbfbfb;
    --field-bg: #f3f3f3;
    --stage: #ecebe8;
  }
  * { box-sizing: border-box; margin: 0; padding: 0; }
  html, body {
    width: 1200px; height: 987px; overflow: hidden;
    background: var(--stage);
    font-family: "Open Sans", Arial, sans-serif;
  }
  .card {
    position: absolute; left: 293px; width: 615px; height: 352px;
    border-radius: 20px; overflow: hidden;
    box-shadow: 0 3px 8px rgba(0,0,0,0.18);
  }
  .card--front { top: 130px; background: var(--card-white); }
  .card--back { top: 505px; background: var(--brand-blue); color: #fff; }

  .brand {
    position: absolute; right: 27px; top: 30px; width: 300px;
    display: flex; flex-direction: column; align-items: center;
  }
  .brand__mark { width: 56px; height: 56px; background: var(--brand-blue); border-radius: 3px; }
  .brand__name {
    margin-top: 10px; font-size: 29px; font-weight: 600;
    letter-spacing: 1.5px; color: var(--brand-blue); text-transform: uppercase; line-height: 1;
  }

  .accent-tab {
    position: absolute; left: 0; top: 178px; width: 12px; height: 51px;
    background: var(--brand-blue); border-radius: 0 6px 6px 0;
  }
  .person { position: absolute; left: 33px; top: 178px; right: 27px; }
  .person__name { font-size: 21px; font-weight: 700; color: var(--brand-deep); line-height: 1.1; }
  .person__name span { font-size: 16px; font-weight: 600; }
  .person__role { font-size: 16px; color: var(--text-grey); margin-top: 2px; }
  .rule { position: absolute; left: 33px; right: 27px; top: 232px; height: 1px; background: var(--rule-grey); }

  .contact { position: absolute; left: 33px; top: 239px; list-style: none; font-size: 16px; color: var(--text-grey); line-height: 23.4px; }
  .contact b { color: var(--brand-deep); font-weight: 700; }
  .address { position: absolute; right: 27px; top: 267px; text-align: right; font-size: 16px; color: var(--text-grey); line-height: 22px; font-style: normal; }

  .back-brand { position: absolute; top: 40px; left: 0; right: 0; display: flex; flex-direction: column; align-items: center; }
  .back-brand__mark { width: 80px; height: 80px; background: #fff; border-radius: 3px; }
  .back-brand__name { margin-top: 12px; font-size: 22px; font-weight: 600; letter-spacing: 1.5px; text-transform: uppercase; }

  .appointment__title { position: absolute; top: 222px; left: 0; right: 0; text-align: center; font-size: 21px; font-weight: 600; }
  .appointment__field {
    position: absolute; left: 30px; width: 556px; top: 273px; height: 43px;
    background: var(--field-bg); border-radius: 22px;
    color: var(--brand-blue); font-style: italic; font-size: 17px;
  }
  .appointment__field span { position: absolute; top: 10px; }
  .field-date { left: 22px; }
  .field-time { left: 300px; }
  .field-ampm { right: 22px; }
  .field-divider { position: absolute; left: 277px; top: 6px; width: 1px; height: 31px; background: var(--brand-blue); }
</style>
</head>
<body>
  <section class="card card--front">
    <div class="brand">
      <div class="brand__mark"></div>
      <div class="brand__name">Veltrimora</div>
    </div>
    <div class="accent-tab"></div>
    <div class="person">
      <h1 class="person__name">LIAM DORSETT <span>BDT, PGDipCDentTech Calverin</span></h1>
      <p class="person__role">Dental Prosthetist</p>
    </div>
    <div class="rule"></div>
    <ul class="contact">
      <li><b>P :</b> 0800 47 3125</li>
      <li><b>C :</b> 09 572 1394</li>
      <li>liam@veltrimora.co.nz</li>
      <li>www.veltrimora.co.nz</li>
    </ul>
    <address class="address">
      14 Marlow Crest Road<br>Halbrook West<br>Auckland 0793
    </address>
  </section>

  <section class="card card--back">
    <div class="back-brand">
      <div class="back-brand__mark"></div>
      <div class="back-brand__name">Veltrimora</div>
    </div>
    <h2 class="appointment__title">NEXT APPOINTMENT</h2>
    <div class="appointment__field">
      <span class="field-date">date:</span>
      <div class="field-divider"></div>
      <span class="field-time">time:</span>
      <span class="field-ampm">am/pm</span>
    </div>
  </section>
</body>
</html>
```